Dalvick's Business Card

I need some designs for a new business card including the new logo attached. An old example of our business card is also attached to show all the data that should be included on the new design.
**I added some more examples someone had mocked up**

Contact Information for Business Card

Should include all info on other examples uploaded.

```html
<!DOCTYPE html>
<html lang="en">
<head>
<meta charset="UTF-8">
<title>Dalvick's Business Card</title>
<link href="https://fonts.googleapis.com/css2?family=Montserrat:wght@400;500;600;700;800&display=swap" rel="stylesheet">
<style>
  :root {
    --blue: #0c66b1;
    --red: #d81f26;
    --card: #f3f3f3;
    --bg: #e4e3e1;
    --white: #ffffff;
  }
  * { margin: 0; padding: 0; box-sizing: border-box; }
  html, body { width: 1200px; height: 1200px; overflow: hidden; }
  body {
    background: var(--bg);
    font-family: "Montserrat", sans-serif;
    position: relative;
  }
  .card {
    position: absolute;
    left: 235px;
    width: 730px;
    height: 416px;
    background: var(--card);
    overflow: hidden;
  }
  .card-front { top: 160px; }
  .card-back { top: 632px; }

  .service-area {
    position: absolute;
    left: 237px; top: 62px;
    font-size: 17px; font-weight: 600; line-height: 23px;
    letter-spacing: 0.2px;
  }
  .blue { color: var(--blue); }
  .red { color: var(--red); font-weight: 700; }

  .brand-mark {
    position: absolute;
    left: 104px; top: 140px;
    width: 110px; height: 110px;
    border-radius: 50%;
    border: 8px solid var(--blue);
  }
  .brand-name {
    position: absolute;
    left: 233px; top: 160px;
    font-size: 70px; font-weight: 600; line-height: 1;
    color: var(--blue);
    letter-spacing: 1px;
  }
  .brand-descriptor {
    position: absolute;
    left: 237px; top: 232px;
    font-size: 18.5px; font-weight: 600;
    color: var(--red);
    letter-spacing: 0.2px;
  }
  .services {
    position: absolute;
    left: 237px; top: 312px;
    font-size: 17px; font-weight: 600; line-height: 24px;
    letter-spacing: 0.2px;
  }

  .bands { position: absolute; left: 0; top: 0; }
  .band-label {
    position: absolute;
    left: 0; width: 100%;
    text-align: center;
    color: var(--white);
    font-size: 22px; font-weight: 400;
    letter-spacing: 0.5px;
  }
  .band-top-label { top: 17px; }
  .band-bottom-label { top: 369px; }

  .holder-name {
    position: absolute;
    left: 80px; top: 150px;
    font-size: 32px; font-weight: 800;
    color: var(--red);
    letter-spacing: 0.3px;
  }
  .contact {
    position: absolute;
    left: 80px;
    display: flex; align-items: center; gap: 9px;
    font-size: 21.5px; font-weight: 400;
    color: var(--blue);
  }
  .contact svg { width: 18px; height: 18px; fill: var(--red); }
  .contact-phone { top: 206px; }
  .contact-email { top: 239px; }

  .back-brand {
    position: absolute;
    left: 470px; top: 150px;
    width: 200px;
    display: flex; flex-direction: column; align-items: center; gap: 12px;
  }
  .back-brand-mark {
    width: 70px; height: 70px;
    border-radius: 50%;
    border: 6px solid var(--blue);
  }
  .back-brand-name {
    font-size: 34px; font-weight: 600;
    color: var(--blue);
    letter-spacing: 0.5px;
  }
</style>
</head>
<body>

<section class="card card-front">
  <p class="service-area">
    <span class="blue">SERVES MAPLE FALLS, IA &amp;</span><br>
    <span class="red">SURROUNDING AREAS</span>
  </p>
  <div class="brand-mark"></div>
  <h1 class="brand-name">DALVICK'S</h1>
  <p class="brand-descriptor">AIR CONDITIONING &amp; HEATING SERVICE</p>
  <p class="services">
    <span class="blue">CALL TODAY FOR ALL YOUR</span> <span class="red">HVAC,</span><br>
    <span class="red">REFRIGERATION</span> <span class="blue">&amp;</span> <span class="red">PLUMBING NEEDS</span>
  </p>
</section>

<section class="card card-back">
  <svg class="bands" width="730" height="416" viewBox="0 0 730 416">
    <rect x="0" y="0" width="730" height="28" fill="var(--blue)"/>
    <rect x="0" y="28" width="730" height="11" fill="var(--red)"/>
    <path d="M200 20 L526 20 L526 28 Q520 28 514 39 L506 54 Q501 62 490 62 L236 62 Q225 62 220 54 L212 39 Q206 28 200 28 Z" fill="var(--blue)"/>
    <rect x="0" y="378" width="730" height="11" fill="var(--red)"/>
    <rect x="0" y="389" width="730" height="27" fill="var(--blue)"/>
    <path d="M156 400 L573 400 L573 389 Q566 389 560 378 L552 364 Q547 356 536 356 L193 356 Q182 356 177 364 L169 378 Q163 389 156 389 Z" fill="var(--blue)"/>
  </svg>
  <p class="band-label band-top-label">LICENSED &amp; INSURED</p>
  <p class="band-label band-bottom-label">FAMILY OWNED &amp; OPERATED</p>

  <h2 class="holder-name">MARK DALVICK</h2>
  <p class="contact contact-phone">
    <svg viewBox="0 0 24 24" aria-hidden="true"><path d="M6.6 10.8a15.1 15.1 0 0 0 6.6 6.6l2.2-2.2c.3-.3.7-.4 1-.2 1.1.4 2.3.6 3.6.6.6 0 1 .4 1 1V20c0 .6-.4 1-1 1A17 17 0 0 1 3 4c0-.6.4-1 1-1h3.5c.6 0 1 .4 1 1 0 1.3.2 2.5.6 3.6.1.3 0 .7-.2 1z"/></svg>
    555.014.2290
  </p>
  <p class="contact contact-email">
    <svg viewBox="0 0 24 24" aria-hidden="true"><path d="M2 5h20v14H2z M2 5l10 8 10-8" fill="var(--red)"/><path d="M3 6l9 7 9-7" fill="none" stroke="#f3f3f3" stroke-width="1.6"/></svg>
    hvacdalvick@mailbox.com
  </p>

  <div class="back-brand">
    <div class="back-brand-mark"></div>
    <span class="back-brand-name">DALVICK'S</span>
  </div>
</section>

</body>
</html>
```